Valdane Companies Business Card Design

We need a new business card for our Private Equity Real Estate Development firm, “Valdane” and our EB-5 regional center “Thornmere Regional Center” on one card. We prefer a design that is simple, elegant, and represents the luxury products we design and build as well as the financial security and stability our successful history has produced. We are an industry leader in our field and 3rd generation family business that has evolved into an institutional quality investment platform. Considered design size is standard business card dimensions (3.5 x 2 inches with an additional 1/8 inch space for design elements or backgrounds that extend beyond the finished size of your piece.

Target Market(s)

• High net worth individuals
• Highly skilled technical workers and physicians in the US seeking investment-based immigration opportunities
• Sophisticated private equity investors
• Intermediary partners include domestic attorneys and investment brokers, as well as international agent networks
• US real estate developers

Industry/Entity Type

Finance

Contact Information for Business Card

(Providing placeholder info for personal information, please design for longer character spaces, longer names and addresses etc..)
• Logo for Valdane
• Logo for Thornmere Regional Center
• Full name: Marcus Valdane
• Job title: CEO
• Email address: mvaldane@valdanecompanies.com
• Cell phone number: +1.555.314.2287
• Office number +1.555.628.4410
• Office address: Larkfield Court 5, 4817 Vista Orilla, Alder Vale, AV.
• Website: www.valdanecompanies.com

Font styles to use
Serif
Sans Serif

Colors
ec1f27
ffffff
000000

Requirements
Must have
• • Logo for Valdane
• • Logo for Thornmere Regional Center
• - Use rounded corners
• (See .ai file included for logos)
Nice to have
• • Simple, elegant design
• • Aesthetically compatible with our website design (www.valdanecompanies.com)
• • Color palette including but not limited to white, black, and red (as per logos)
Should not have
• - Not too much red color
• - Do not stack both logos on top of each other

```html
<!DOCTYPE html>
<html lang="en">
<head>
<meta charset="utf-8">
<title>Valdane Companies – Business Card</title>
<link rel="stylesheet" href="https://fonts.googleapis.com/css2?family=Roboto:wght@400;500;700&display=swap">
<style>
  :root {
    --stage: #2b2b2b;
    --card-light: #ffffff;
    --card-dark: #262626;
    --brand-red: #ec1f27;
    --logo-red: #a3142e;
    --ink-white: #ffffff;
    --ink-soft: #e6e6e6;
  }
  * { box-sizing: border-box; margin: 0; padding: 0; }
  html, body {
    width: 1200px; height: 1200px; overflow: hidden;
    background: var(--stage);
    font-family: "Roboto", Arial, sans-serif;
  }
  .stage {
    width: 1200px; height: 1200px;
    display: flex; flex-direction: column; align-items: center; justify-content: center;
    gap: 48px;
  }
  .card {
    width: 700px; height: 400px;
    border-radius: 8px;
    position: relative;
    overflow: hidden;
    box-shadow: 0 10px 30px rgba(0,0,0,.35);
  }
  .card-front {
    background: var(--card-light);
    display: flex; align-items: center; justify-content: center;
  }
  .front-wordmark {
    color: var(--logo-red);
    font-weight: 500;
    font-size: 40px;
    letter-spacing: 3px;
    text-transform: uppercase;
    text-align: center;
    line-height: 1.25;
  }
  .card-back {
    background: var(--card-dark);
    display: flex; align-items: center;
    padding: 0 40px 0 48px;
  }
  .back-wordmark {
    display: flex; align-items: center; gap: 14px;
    width: 300px; flex: none;
  }
  .back-wordmark .mark-square {
    width: 34px; height: 34px; background: var(--ink-soft); flex: none;
  }
  .back-wordmark .mark-name {
    color: var(--ink-soft);
    font-weight: 500;
    font-size: 19px;
    letter-spacing: 2px;
    text-transform: uppercase;
    line-height: 1.3;
  }
  .divider {
    width: 1px; height: 150px; background: var(--brand-red);
    margin: 0 28px 0 14px; flex: none;
  }
  .contact { color: var(--ink-white); white-space: nowrap; }
  .contact-name { font-size: 24px; font-weight: 700; line-height: 1.1; }
  .contact-name .surname { color: var(--brand-red); }
  .contact-title { font-size: 14px; margin: 4px 0 14px; color: var(--ink-soft); }
  .contact-list { list-style: none; font-size: 14px; line-height: 1.55; }
  .contact-list li { display: flex; align-items: flex-start; gap: 12px; }
  .contact-list svg { width: 14px; height: 14px; margin-top: 4px; flex: none; fill: var(--brand-red); }
  .contact-list .addr { display: block; }
</style>
</head>
<body>
<main class="stage">
  <section class="card card-front" aria-label="Card front">
    <div class="front-wordmark">Thornmere<br>Regional Center</div>
  </section>

  <section class="card card-back" aria-label="Card back">
    <div class="back-wordmark">
      <span class="mark-square"></span>
      <span class="mark-name">Thornmere<br>Regional Center</span>
    </div>
    <div class="divider"></div>
    <div class="contact">
      <p class="contact-name">Marcus <span class="surname">Valdane</span></p>
      <p class="contact-title">CEO</p>
      <ul class="contact-list">
        <li>
          <svg viewBox="0 0 14 14"><path d="M4 0h6a1 1 0 0 1 1 1v12a1 1 0 0 1-1 1H4a1 1 0 0 1-1-1V1a1 1 0 0 1 1-1zm0.8 1.5v9.5h4.4V1.5z"/></svg>
          <span>+1.555.314.2287</span>
        </li>
        <li>
          <svg viewBox="0 0 14 14"><path d="M1 4c0-2 2-3 6-3s6 1 6 3v1.5H9.5V4h-5v1.5H1zM3 7h8l2 6H1z"/></svg>
          <span>+1.555.628.4410</span>
        </li>
        <li>
          <svg viewBox="0 0 14 14"><path d="M0 3h14v8H0zM1.2 4v.4L7 8l5.8-3.6V4L7 7.5z"/></svg>
          <span>mvaldane@valdanecompanies.com</span>
        </li>
        <li>
          <svg viewBox="0 0 14 14"><path d="M7 0a7 7 0 1 0 0 14A7 7 0 0 0 7 0zm-1 1.2C5 2.6 4.5 4.6 4.4 6.3H1.3A5.8 5.8 0 0 1 6 1.2zm2 0a5.8 5.8 0 0 1 4.7 5.1H9.6C9.5 4.6 9 2.6 8 1.2zM7 1.5c.9 1.3 1.4 3 1.5 4.8h-3C5.6 4.5 6.1 2.8 7 1.5zM1.3 7.7h3.1c.1 1.7.6 3.7 1.6 5.1a5.8 5.8 0 0 1-4.7-5.1zm4.2 0h3c-.1 1.8-.6 3.5-1.5 4.8-.9-1.3-1.4-3-1.5-4.8zm4.1 0h3.1A5.8 5.8 0 0 1 8 12.8c1-1.4 1.5-3.4 1.6-5.1z"/></svg>
          <span>www.valdanecompanies.com</span>
        </li>
        <li>
          <svg viewBox="0 0 14 14" aria-hidden="true"></svg>
          <span>
            <span class="addr">Larkfield Court 5, 4817</span>
            <span class="addr">Vista Orilla Alder Vale, AV</span>
          </span>
        </li>
      </ul>
    </div>
  </section>
</main>
</body>
</html>
```